Counselling business needs a DL brochure design ready for print next week!

My business is called Quiet Harbour Counselling. My name is Megan Trelawny and I'm a qualified Psychotherapist based in Sydney, Australia.

I need a DL brochure to promote my business. I like the idea of possibly incorporating a leaf/leaves and/or the colour green in a sophisticated, understated way in the DL design. I have attached a leaf image for reference. I am looking for a simple, elegant design overall. Not too many fonts, something which is easy to read and captures people's interest.

I need a print ready design - something that my local instant printer can use easily. I need a print ready PDF and original files too for the printer. I am anticipating that the design will be A4 folded to DL as it needs to fit into standard dimension plastic DL stands at various locations.

My business is focussed upon helping people overcome difficulties such as grief or anxiety. I also work with people to help them plan their life adventures. My business is different from the average counselling business. For example, I give my clients a beautiful thick stock postcard at the end of every session with takeaway learnings and insights which they've uncovered. That way, they can reflect upon those discoveries and capitalise upon them.

I have an office in a local wellness centre. The brochure will be showcased at the centre and in local medical centres and shops. The aim is that new prospects will pick up the brochure and be prompted to call me for a counselling appointment.

I have attached copy for my DL brochure and a competitor's DL for reference. I'm not seeking to emulate the competitor, but I thought that it could be a useful reference - the competitor DL is clear and easy to read. I need my photo to be included in the brochure, adjacent to the information about my background. I have attached a reference photo for use as a positional - a full size image will need to be dropped in as part of this job by the winning designer.

I do not have a company logo at the moment, but I need my business name and contact details repeated several times in the DL.
Updates

Hello. Thank you for your designs. I am so pleased to have received them. I will be in touch in the next 24 hours. Best, Megan

Industry/Entity Type

Business

```html
<!DOCTYPE html>
<html lang="en">
<head>
<meta charset="utf-8">
<title>Quiet Harbour Counselling – DL Brochure</title>
<link href="https://fonts.googleapis.com/css2?family=Maven+Pro:wght@400;500;600;700&display=swap" rel="stylesheet">
<style>
  :root {
    --green: #8dbb3f;
    --green-dark: #6f9e2a;
    --panel-grey: #f0f0f0;
    --faint-green: #e2e8d6;
    --ink: #333333;
    --ink-soft: #555555;
    --white: #ffffff;
    --fold-line: #dcdcdc;
  }
  * { margin: 0; padding: 0; box-sizing: border-box; }
  html, body { width: 1200px; height: 876px; overflow: hidden; background: var(--white); }
  body { font-family: "Maven Pro", sans-serif; color: var(--ink); }

  .brochure { position: relative; width: 1200px; height: 876px; }
  .brochure-shapes { position: absolute; inset: 0; }

  .brand {
    position: absolute; display: flex; align-items: center;
  }
  .brand-dot { border-radius: 50%; background: var(--green); flex: none; }
  .brand-name {
    color: var(--green); font-weight: 600; text-transform: uppercase;
    line-height: 1.05; letter-spacing: 0.02em;
  }

  /* Left panel */
  .intro-heading {
    position: absolute; left: 0; width: 400px; top: 44px;
    text-align: center; color: var(--green);
    font-size: 27px; font-weight: 600; line-height: 35px;
  }
  .intro-copy {
    position: absolute; left: 35px; width: 335px; top: 136px;
    font-size: 18.5px; line-height: 28.5px; color: var(--ink-soft);
  }
  .intro-copy strong { font-weight: 700; color: var(--ink); }
  .leaf-photo {
    position: absolute; left: 110px; top: 456px; width: 181px; height: 279px;
    background: linear-gradient(180deg, #5e9a2c 0%, #a9cf6c 38%, #f3f6ef 55%, #eef4e6 72%, #7fb447 100%);
  }
  .brand--left { left: 54px; top: 776px; }
  .brand--left .brand-dot { width: 68px; height: 68px; margin-right: 14px; }
  .brand--left .brand-name { font-size: 28px; }

  /* Middle panel */
  .tagline {
    position: absolute; left: 400px; width: 400px; top: 386px;
    text-align: center; font-size: 24px; font-weight: 600; line-height: 37px; color: var(--ink);
  }
  .tagline-accent {
    position: absolute; left: 400px; width: 400px; top: 496px;
    text-align: center; font-size: 24px; font-weight: 600; line-height: 37px; color: var(--green);
  }
  .brand--middle { right: 422px; top: 690px; }
  .brand--middle .brand-dot { width: 48px; height: 48px; margin-right: 10px; }
  .brand--middle .brand-name { font-size: 20px; }
  .contact {
    position: absolute; right: 422px; top: 753px; text-align: right; color: var(--ink-soft);
  }
  .contact-line { display: flex; align-items: center; justify-content: flex-end; gap: 5px; }
  .contact-address { font-size: 14px; height: 20px; }
  .contact-phone { font-size: 23px; font-weight: 600; color: var(--ink); height: 36px; }
  .contact-email, .contact-web { font-size: 14px; height: 24px; }
  .contact svg { flex: none; }

  /* Right panel */
  .hero-photo {
    position: absolute; left: 800px; top: 150px; width: 400px; height: 560px;
    background: linear-gradient(135deg, #4f7a2a 0%, #8cab52 40%, #b7c98a 60%, #6f9440 100%);
  }
  .brand--cover { left: 839px; top: 58px; }
  .brand--cover .brand-dot { width: 76px; height: 76px; margin-right: 14px; }
  .brand--cover .brand-name { font-size: 28px; }
  .cover-line {
    position: absolute; left: 800px; width: 400px; text-align: center;
    font-size: 26px; font-weight: 600;
  }
  .cover-line--dark { top: 780px; color: var(--ink); }
  .cover-line--green { top: 821px; color: var(--green); }
</style>
</head>
<body>
<main class="brochure">
  <svg class="brochure-shapes" width="1200" height="876" viewBox="0 0 1200 876" aria-hidden="true">
    <rect class="panel-left" x="0" y="0" width="400" height="876" fill="var(--panel-grey)"/>
    <rect class="panel-middle" x="400" y="0" width="400" height="876" fill="var(--panel-grey)"/>
    <rect class="panel-right" x="800" y="0" width="400" height="876" fill="var(--white)"/>
    <line x1="400" y1="0" x2="400" y2="876" stroke="var(--fold-line)" stroke-width="1"/>
    <line x1="800" y1="0" x2="800" y2="876" stroke="var(--fold-line)" stroke-width="1"/>
  </svg>

  <div class="hero-photo" role="img" aria-label="Photo of a woman in a green top stretching her arms out in a sunny park"></div>

  <svg class="brochure-shapes" width="1200" height="876" viewBox="0 0 1200 876" aria-hidden="true">
    <!-- top swoosh -->
    <path class="top-white" d="M444,0 C520,110 650,185 800,196 C950,205 1100,170 1200,135 L1200,0 Z" fill="var(--white)"/>
    <path class="top-band" d="M444,0 C520,110 650,185 800,196 C950,205 1100,170 1200,135 L1200,172 C1100,198 960,214 800,207 C680,200 560,120 482,0 Z" fill="var(--green)"/>
    <path d="M478,0 C560,120 680,203 800,211 C960,218 1100,202 1200,176" fill="none" stroke="var(--white)" stroke-width="5"/>
    <!-- bottom arch -->
    <path class="bottom-white" d="M400,830 C520,720 650,672 800,668 C950,665 1100,720 1200,790 L1200,876 L400,876 Z" fill="var(--white)"/>
    <path class="bottom-band" d="M400,800 C520,700 650,648 800,643 C950,640 1100,692 1200,752 L1200,790 C1100,720 950,665 800,668 C650,672 520,720 400,830 Z" fill="var(--green)"/>
    <path d="M400,797 C520,697 650,644 800,639 C950,636 1100,688 1200,748" fill="none" stroke="var(--white)" stroke-width="5"/>
    <!-- faint emblem circle -->
    <circle cx="600" cy="283" r="80" fill="var(--faint-green)"/>
  </svg>

  <!-- Left panel -->
  <h2 class="intro-heading">DO YOU NEED<br>A POSITIVE CHANGE?</h2>
  <p class="intro-copy"><strong>DO YOU WISH</strong> You felt more joyful and fulfilled? You felt less stressed or overwhelmed? You coped better with life’s challenges? You could break unhelpful habits? DO YOU IMAGINE Your relationships being closer? Your life being well balanced? Your goals being within reach? Your life being more adventurous?</p>
  <div class="leaf-photo" role="img" aria-label="Photo of a green leaf dripping a water drop into rippling water"></div>
  <div class="brand brand--left">
    <span class="brand-dot"></span>
    <span class="brand-name">Quiet Harbour<br>Counselling</span>
  </div>

  <!-- Middle panel -->
  <p class="tagline">The power to create new<br>possibilities is within you.</p>
  <p class="tagline-accent">You might just need<br>a helping hand</p>
  <div class="brand brand--middle">
    <span class="brand-dot"></span>
    <span class="brand-name">Quiet Harbour<br>Counselling</span>
  </div>
  <address class="contact" style="font-style:normal">
    <div class="contact-line contact-address">
      <svg width="10" height="13" viewBox="0 0 10 13"><path d="M5 0C2.2 0 0 2.2 0 4.8 0 8.5 5 13 5 13s5-4.5 5-8.2C10 2.2 7.8 0 5 0zm0 6.7A1.9 1.9 0 1 1 5 2.9a1.9 1.9 0 0 1 0 3.8z" fill="var(--ink-soft)"/></svg>
      12-48 Harbourview Lane Port Ellison
    </div>
    <div class="contact-line contact-phone">
      <svg width="20" height="20" viewBox="0 0 20 20"><circle cx="10" cy="10" r="9" fill="none" stroke="var(--ink)" stroke-width="1.5"/><path d="M7 5.5l1.6 2.3-1 1.2c.6 1.3 1.5 2.2 2.8 2.8l1.2-1 2.3 1.6-.9 1.7c-3.7-.3-6.4-3-6.7-6.7z" fill="var(--ink)"/></svg>
      604-555-0182
    </div>
    <div class="contact-line contact-email">
      <svg width="14" height="10" viewBox="0 0 14 10"><rect x=".5" y=".5" width="13" height="9" fill="none" stroke="var(--ink-soft)"/><path d="M.5.5L7 6l6.5-5.5" fill="none" stroke="var(--ink-soft)"/></svg>
      hello@quietharbourcounselling.com
    </div>
    <div class="contact-line contact-web">
      <svg width="13" height="13" viewBox="0 0 13 13"><circle cx="6.5" cy="6.5" r="6" fill="none" stroke="var(--ink-soft)"/><ellipse cx="6.5" cy="6.5" rx="2.6" ry="6" fill="none" stroke="var(--ink-soft)"/><path d="M.5 6.5h12" stroke="var(--ink-soft)"/></svg>
      www.quietharbourcounselling.com
    </div>
  </address>

  <!-- Right panel (cover) -->
  <div class="brand brand--cover">
    <span class="brand-dot"></span>
    <span class="brand-name">Quiet Harbour<br>Counselling</span>
  </div>
  <p class="cover-line cover-line--dark">Overcome Difficulties and</p>
  <p class="cover-line cover-line--green">Make A Fresh Start</p>
</main>
</body>
</html>
```